Business Card Design for Vintage Jazz

I am a vintage jazz band leader in New York City. My groups play the music of the 1920s, 1930s and 1940s. My website is morvalquist.com for more info on what I do.

I am looking for a two sided business card design that has the look and feel of a really nice business card from the 1930s. I need to convey with the design that my work has that vintage kind of class and style, but also conveys that we are fun and entertaining.

Most importantly it should make a bold staement. If Hal Denbrook had a card, what would it have looked like? I want a card that I feel confident will make an impact and will let people know that my work is te the top that NYC has to offer in vintage jazz..

Note that I have only decided to avoid the "committed payment" option as I have not used this service before. Assuming that I get quality work I will select a design from those presented.

Target Market(s)

people who want to hire my band for events, media, and new fans of the band

Industry/Entity Type

Performing Art

Contact Information for Business Card

Definitely a matte finish, possibly a sort of old style of paper with that brown tint? definitely a thick card.

Requirements
Must have
• FRONT
• My name: Tobin Vashley
• What I do: Bandleader, Guitarist, Vocalist, Songwriter
• Contact Details: morvalquist.com tobin@morvalquist.com 646-555-0148
• BACK
• My Social Media Links:
• facebook.morvalquist.com
• twitter, instagram, linkedin: morvalquist
• I'm also including a photo image I would like to use. The photo's background is not needed, and to be honest isn't really desireable. Just looking to use the image of me.
Nice to have
• I'm attaching which could be used as is, omitted from the card, or altered maybe with text going around the outside of the circle or in some other way. It may need some clean up to the edges of the lettering as we only use it for the website thumbnail.
• If there's space I'd like to include the text "join our mailing list for a free song download: freesong.morvalquist.com" If not perhaps just "Download a Free Song at: freesong.morvalquist.com - something to this end.
Should not have
• anything cartoony. Don't think retro 90s's vision of the swing era, think actual swing era!
• anything modern. Got to look old school
• Try to avoid dark backgrounds. Since we often play in bars and clubs where it is dar, a d
• avoid script fonts.

```html
<!DOCTYPE html>
<html lang="en">
<head>
<meta charset="utf-8">
<title>Tobin Vashley – Business Card</title>
<link href="https://fonts.googleapis.com/css2?family=Ubuntu:wght@400;500;700&display=swap" rel="stylesheet">
<style>
  :root {
    --teal: #5ab5a0;
    --teal-dark: #3f9784;
    --ink: #222222;
    --grey-text: #555555;
    --paper: #f4f4f2;
    --stage: #e9e9e7;
    --photo-dark: #3c3c3c;
    --photo-light: #9a9a9a;
  }
  * { margin: 0; padding: 0; box-sizing: border-box; }
  html, body { width: 1200px; height: 795px; overflow: hidden; }
  body {
    background: var(--stage);
    font-family: "Ubuntu", sans-serif;
    position: relative;
  }
  .card {
    position: absolute;
    top: 243px;
    width: 540px;
    height: 309px;
    border-radius: 22px;
    overflow: hidden;
    box-shadow: 0 6px 18px rgba(0,0,0,0.18);
  }
  /* Front: teal side */
  .card-front { left: 30px; background: var(--teal); }
  .front-photo {
    position: absolute;
    left: 24px; bottom: 0;
    width: 230px; height: 250px;
    border-radius: 110px 110px 0 0;
    background: linear-gradient(160deg, var(--photo-light) 0%, var(--photo-dark) 70%);
  }
  .front-info {
    position: absolute;
    right: 34px; top: 52px;
    width: 270px;
    color: #ffffff;
  }
  .front-name { font-size: 40px; font-weight: 700; letter-spacing: 0.5px; line-height: 1; }
  .front-role { font-size: 13px; margin-top: 10px; }
  .social-row { display: flex; gap: 7px; margin-top: 16px; }
  .social-dot { width: 19px; height: 19px; border-radius: 50%; background: var(--ink); }
  .front-web { font-size: 14px; letter-spacing: 3px; margin-top: 16px; }

  /* Back: white side */
  .card-back { left: 630px; background: var(--paper); }
  .mark {
    position: absolute;
    left: 44px; top: 92px;
    width: 150px; height: 150px;
    border-radius: 50%;
    background: var(--teal);
    display: flex; align-items: center; justify-content: center;
    text-align: center;
    color: var(--ink);
    font-size: 19px; font-weight: 500; line-height: 1.15;
  }
  .back-info { position: absolute; left: 232px; top: 54px; }
  .back-name { color: var(--teal); font-size: 28px; font-weight: 500; }
  .contact-list { list-style: none; margin-top: 18px; }
  .contact-list li {
    display: flex; align-items: center; gap: 8px;
    font-size: 14px; color: var(--ink); margin-bottom: 6px;
  }
  .contact-icon { width: 14px; height: 14px; flex: none; }
  .back-role {
    position: absolute; left: 232px; bottom: 48px;
    font-size: 14px; letter-spacing: 1.5px; color: var(--grey-text);
  }
</style>
</head>
<body>

<section class="card card-front">
  <div class="front-photo" role="img" aria-label="Black and white photo of the bandleader in a striped blazer tipping a straw boater hat"></div>
  <div class="front-info">
    <h1 class="front-name">Tobin Vashley</h1>
    <p class="front-role">Bandleader, Guitarist, Vocalist, Songwriter</p>
    <div class="social-row" aria-label="Social media links">
      <span class="social-dot"></span><span class="social-dot"></span><span class="social-dot"></span>
      <span class="social-dot"></span><span class="social-dot"></span><span class="social-dot"></span>
      <span class="social-dot"></span><span class="social-dot"></span>
    </div>
    <p class="front-web">www.morvalquist.com</p>
  </div>
</section>

<section class="card card-back">
  <div class="mark">Tobin<br>Vashley</div>
  <div class="back-info">
    <h2 class="back-name">Tobin Vashley</h2>
    <ul class="contact-list">
      <li>
        <svg class="contact-icon" viewBox="0 0 14 14"><circle cx="7" cy="7" r="7" fill="#5ab5a0"/><path d="M4.5 3.5l1.5 0 .6 1.8-.9.7a5 5 0 0 0 2.3 2.3l.7-.9 1.8.6 0 1.5c-3.5.3-6.3-2.5-6-6z" fill="#fff"/></svg>
        646-555-0148
      </li>
      <li>
        <svg class="contact-icon" viewBox="0 0 14 14"><circle cx="7" cy="7" r="7" fill="#5ab5a0"/><rect x="3.5" y="4.5" width="7" height="5" fill="none" stroke="#fff" stroke-width="1"/><path d="M3.5 4.5l3.5 3 3.5-3" fill="none" stroke="#fff" stroke-width="1"/></svg>
        tobin@morvalquist.com
      </li>
      <li>
        <svg class="contact-icon" viewBox="0 0 14 14"><circle cx="7" cy="7" r="7" fill="#5ab5a0"/><circle cx="7" cy="7" r="3.8" fill="none" stroke="#fff" stroke-width="0.9"/><path d="M3.2 7h7.6M7 3.2v7.6" stroke="#fff" stroke-width="0.9"/></svg>
        www.morvalquist.com
      </li>
    </ul>
  </div>
  <p class="back-role">BANDLEADER, GUITARIST, VOCALIST, SONGWRITER</p>
</section>

</body>
</html>
```